Heron Property Inspection business card

I am the principal inspector of Heron Property Inspections. I serve Northern Virginia from Winchester to Arlington.Associate, Federated Guild of Dwelling Examiners (FGDE)Graduate, FGDE Home Inspectors CourseNational Association of Home Inspectors ExamI'd like the business card to look more professional than comical.I pulled the attached picture off the web. I'd like to have something like that or an image of a house as my logo on the cards.

Target Market(s)

Persons who recently purchased a home.

Industry/Entity Type

Business

Contact Information for Business Card

Bob AllenBadger Home Inspections, LLC.4455 River RoadBluemont, Virginia 20135cell: 703-231-6680e-mail: tkmarlow@postvale.net

Font styles to use
Serif
Sans Serif

Requirements
Must have
• I'd like to have a logo, something that identifies me as a home inspector. The attached images are something that I'd like to have incorporated into my business card logo.
Nice to have
• I'd like a sketch of a house and/or a magnifying glass showing a house being inspected. The attached images are used as a suggestion only, I do not own the images.
Should not have
• Gimmicky stuff. I want to appear professional and trustworthy.

```html
<!DOCTYPE html>
<html lang="en">
<head>
<meta charset="utf-8">
<title>Heron Property Inspection – Business Card</title>
<link href="https://fonts.googleapis.com/css2?family=Tinos:wght@400;700&display=swap" rel="stylesheet">
<style>
  :root {
    --page-bg: #ecebe8;
    --card-white: #ffffff;
    --brand-blue: #1d74c4;
    --brand-blue-deep: #0f5fa8;
    --brand-blue-light: #3c97dd;
    --brand-navy: #223a7a;
    --photo-light: #d9dde0;
    --photo-mid: #a9b0b4;
    --photo-green: #6f8a5c;
    --text-on-blue: #ffffff;
  }
  html, body {
    margin: 0;
    padding: 0;
    width: 1200px;
    height: 892px;
    overflow: hidden;
    background: var(--page-bg);
  }
  .canvas {
    position: relative;
    width: 1200px;
    height: 892px;
  }
  .business-card {
    position: absolute;
    left: 50px;
    top: 132px;
    width: 1100px;
    height: 628px;
    background: var(--card-white);
    box-shadow: 0 6px 24px rgba(0,0,0,0.18);
    overflow: hidden;
  }
  .card-shapes {
    position: absolute;
    inset: 0;
  }
  .brand-lockup {
    position: absolute;
    right: 60px;
    top: 150px;
    display: flex;
    align-items: center;
    gap: 16px;
    font-family: "Tinos", serif;
    font-weight: 700;
    font-size: 34px;
    color: var(--brand-navy);
    white-space: nowrap;
  }
  .brand-dot {
    width: 26px;
    height: 26px;
    border-radius: 50%;
    background: var(--brand-blue);
  }
  .contact-block {
    position: absolute;
    right: 52px;
    top: 330px;
    text-align: right;
    font-family: "Tinos", serif;
    color: var(--text-on-blue);
  }
  .employee-name {
    font-size: 50px;
    font-weight: 700;
    line-height: 1;
    margin: 0;
  }
  .employee-title {
    font-size: 20px;
    margin: 6px 0 28px;
  }
  .contact-line {
    display: flex;
    justify-content: flex-end;
    align-items: center;
    gap: 14px;
    font-size: 29px;
    line-height: 1.18;
  }
  .contact-line svg {
    flex: none;
    width: 24px;
    height: 24px;
  }
  .contact-address {
    align-items: flex-start;
  }
  .contact-address svg { margin-top: 6px; }
  .address-text { display: block; }
</style>
</head>
<body>
<div class="canvas">
  <div class="business-card">
    <svg class="card-shapes" viewBox="0 0 1100 628" width="1100" height="628" aria-hidden="false">
      <defs>
        <linearGradient id="photoTone" x1="0" y1="0" x2="0.4" y2="1">
          <stop offset="0" stop-color="var(--photo-light)"/>
          <stop offset="0.65" stop-color="var(--photo-mid)"/>
          <stop offset="1" stop-color="var(--photo-green)"/>
        </linearGradient>
        <linearGradient id="bandTone" x1="0" y1="0" x2="1" y2="1">
          <stop offset="0" stop-color="var(--brand-blue-light)"/>
          <stop offset="0.5" stop-color="var(--brand-blue)"/>
          <stop offset="1" stop-color="var(--brand-blue-deep)"/>
        </linearGradient>
      </defs>
      <polygon class="house-photo" role="img" aria-label="Photo of a two-storey house with a magnifying glass inspecting its upper window"
               points="0,0 460,0 600,290 320,628 0,628" fill="url(#photoTone)"/>
      <line class="accent-line" x1="460" y1="0" x2="600" y2="290" stroke="var(--brand-blue)" stroke-width="10"/>
      <polygon class="contact-band" points="600,290 1100,250 1100,628 320,628" fill="url(#bandTone)"/>
    </svg>

    <div class="brand-lockup">
      <span class="brand-dot"></span>
      <span class="brand-name">Heron Property Inspections, LLC</span>
    </div>

    <div class="contact-block">
      <p class="employee-name">Employee name</p>
      <div class="employee-title">Managing Director</div>
      <div class="contact-line">
        <span>703-555-0192</span>
        <svg viewBox="0 0 24 24"><rect x="1" y="1" width="22" height="22" rx="5" fill="#fff"/><rect x="8" y="5" width="8" height="14" rx="1.5" fill="none" stroke="var(--brand-blue)" stroke-width="2"/></svg>
      </div>
      <div class="contact-line">
        <span>tkmarlow@postvale.net</span>
        <svg viewBox="0 0 24 24"><rect x="1" y="1" width="22" height="22" rx="5" fill="#fff"/><rect x="5" y="7" width="14" height="10" fill="none" stroke="var(--brand-blue)" stroke-width="2"/><polyline points="5,7 12,13 19,7" fill="none" stroke="var(--brand-blue)" stroke-width="2"/></svg>
      </div>
      <div class="contact-line contact-address">
        <span class="address-text">7182 Quarry Lane Fernhill,<br>Virginia 20148</span>
        <svg viewBox="0 0 24 24"><rect x="1" y="1" width="22" height="22" rx="5" fill="#fff"/><path d="M12 5a4.5 4.5 0 0 0-4.5 4.5c0 3.5 4.5 9 4.5 9s4.5-5.5 4.5-9A4.5 4.5 0 0 0 12 5z" fill="var(--brand-blue)"/><circle cx="12" cy="9.5" r="1.7" fill="#fff"/></svg>
      </div>
    </div>
  </div>
</div>
</body>
</html>
```